Landingpage design

We need a landingpage for a Chatterloom add campaign. We sell socks made of bamboo in super quality. Our customers loves us, and we have a 5 heart rating at scorevane.com.

We want to create a add campaign targeted new customers, and the offer is that they can buy 1 pair of bamboo socks as a test, for only 20 DKK (2,7 Euro) including shipment. Our webpage is www.tuvelo.dk, landingpage should be built i Kyvio, a wysiwyg editor. based on their template. like:
https://tuvelo.pemlorsite.com/13844-sales-page
https://tuvelo.pemlorsite.com/13696-sales-page
https://tuvelo.pemlorsite.com/13845-sales-page

You don't have to follow the templates 100% if you have better ideas. We have an account for snapvaultly, so please get stockphotos from here.

Bamboo socks has a lot of great selling points, you can see a good desciption here:
https://feltrano.com/us/why-bamboo

We expect you to have experience in landingpage design, and expect to end up with 2 landingpages we can splittest on.

This is the first of a number of landingpages we need in the future, so for the right person there will be plenty of more work.

Target Market(s)

Denmark

Industry/Entity Type

E-Commerce

Number of Pages Required

2 page

Colors

Designer to choose colors to be used in the design.

Requirements
Must have
• A great selling page, showing all the great things with bamboo socks. It should be supplied with good packshots from snapvaultly.com

```html
<!DOCTYPE html>
<html lang="en">
<head>
<meta charset="utf-8">
<title>Tuvelo – Bamboo Socks Landing Page</title>
<link href="https://fonts.googleapis.com/css2?family=Roboto:wght@300;400;500;700&display=swap" rel="stylesheet">
<style>
:root{
  --green:#2fb37c;
  --green-dark:#26a06d;
  --ink:#2b2f36;
  --muted:#6d737b;
  --light:#f3f4f4;
  --white:#ffffff;
  --footer:#1f2333;
  --star:#f5b921;
  --blue-top:#74d3ee;
  --blue-bottom:#3f8ce8;
  --mint:#e7f2ea;
}
*{box-sizing:border-box;margin:0;padding:0}
html,body{width:1200px;height:5099px;overflow:hidden}
body{font-family:'Roboto',sans-serif;color:var(--ink);background:var(--white)}
.btn{display:inline-block;background:var(--green);color:var(--white);font-size:13px;font-weight:500;text-transform:uppercase;letter-spacing:.5px;padding:11px 34px;border-radius:2px;text-decoration:none}
.btn-ghost{background:transparent;border:1px solid rgba(255,255,255,.8)}
.small-note{font-size:11px;color:var(--muted);margin-top:8px}
h2.section-title{font-size:34px;font-weight:500;text-align:center;color:var(--ink)}
.lead{font-size:15px;line-height:1.6;color:var(--muted);text-align:center}

/* header */
.site-header{height:68px;display:flex;align-items:center;padding:0 135px;background:var(--white)}
.brand{display:flex;align-items:center;gap:10px}
.brand-square{width:40px;height:40px;background:var(--ink)}
.brand-name{font-size:20px;font-weight:700;color:var(--ink)}
.main-nav{margin-left:auto;display:flex;align-items:center;gap:34px;font-size:12px;text-transform:uppercase;color:var(--muted)}
.main-nav .active{color:var(--ink);border-bottom:2px solid var(--green);padding-bottom:4px}
.main-nav .btn{padding:8px 60px;font-size:11px}

/* hero */
.hero{height:492px;position:relative;background:linear-gradient(90deg,#3e3a36 0%,#6b625a 55%,#cfc6bd 100%)}
.hero-photo{position:absolute;inset:0}
.hero-content{position:relative;padding:48px 135px;color:var(--white)}
.hero h1{font-size:44px;font-weight:700;line-height:1.15;width:640px}
.ticks{list-style:none;margin:26px 0 30px}
.ticks li{font-size:15px;margin-bottom:9px;display:flex;align-items:center;gap:10px}
.ticks svg{flex:none}
.hero-actions{display:flex;gap:14px}
.hero .small-note{color:#e8e4e0}

/* why */
.why{height:590px;background:var(--light);padding-top:90px}
.why .lead{width:560px;margin:24px auto 40px}
.benefits{display:flex;justify-content:center;gap:22px}
.benefit{width:213px;height:192px;background:var(--white);text-align:center;padding:28px 18px}
.benefit h3{font-size:16px;font-weight:500;margin:12px 0 8px}
.benefit p{font-size:11px;line-height:1.5;color:var(--muted)}

/* feature rows */
.feature{display:flex;height:327px}
.feature .photo{width:600px;height:100%}
.feature .text{width:600px;padding:90px 50px 0 45px;background:var(--white)}
.feature.alt .text{background:var(--light)}
.feature h3{font-size:28px;font-weight:500;margin-bottom:14px}
.feature p{font-size:15px;line-height:1.6;color:var(--muted);width:470px}
.feature.left-text .text{padding-left:135px}

/* offer band */
.offer-band{height:206px;background:var(--mint);display:flex;align-items:center;padding:0 135px}
.offer-pct{font-size:78px;font-weight:700;color:var(--green);margin-right:30px}
.offer-title{font-size:26px;font-weight:500;line-height:1.25;width:430px}
.offer-cta{margin-left:auto;text-align:right}
.offer-cta .btn{padding:10px 80px}

/* facts */
.facts{height:561px;background:linear-gradient(180deg,var(--blue-top),var(--blue-bottom));color:var(--white);text-align:center;padding-top:95px}
.facts h2{font-size:34px;font-weight:500}
.facts .intro{font-size:15px;line-height:1.6;width:580px;margin:24px auto 62px;font-weight:500}
.fact-row{display:flex;justify-content:center;gap:70px}
.fact{width:240px}
.fact-icon{width:68px;height:68px;border-radius:50%;background:var(--white);margin:0 auto 26px;display:flex;align-items:center;justify-content:center}
.fact p{font-size:14px;line-height:1.6}

/* video */
.video{height:723px;background:#f2f2f1;position:relative;text-align:center;padding-top:100px}
.leaf{position:absolute}
.video .lead{width:580px;margin:20px auto 40px}
.video-frame{width:712px;height:340px;margin:0 auto;position:relative;background:linear-gradient(135deg,#6b4a33,#a07a5a 50%,#3f3a35)}
.play{position:absolute;left:50%;top:50%;transform:translate(-50%,-50%)}

/* rating */
.rating{height:800px;background:var(--white);text-align:center;padding-top:100px;position:relative}
.stars{color:var(--star);font-size:36px;letter-spacing:4px}
.rating .lead{width:320px;margin:18px auto 50px}
.reviews{display:flex;justify-content:center;gap:22px;position:relative}
.review{width:257px;height:268px;background:var(--light);text-align:left;padding:28px 22px}
.reviewer{display:flex;align-items:center;gap:12px;margin-bottom:14px}
.avatar{width:42px;height:42px;border-radius:50%;background:#8b9bb0}
.reviewer strong{display:block;font-size:14px;font-weight:500}
.reviewer span{color:var(--star);font-size:14px}
.review p{font-size:13px;line-height:1.6;color:var(--muted)}
.arrow{position:absolute;top:120px;color:var(--green);font-size:28px}
.rating .btn{margin-top:46px;padding:11px 64px}

/* final CTA */
.final-cta{height:435px;background:#eeeeee;position:relative;padding:74px 135px}
.final-cta h2{font-size:44px;font-weight:700;line-height:1.15;width:640px}
.final-cta .ticks li{color:var(--muted);font-size:14px;margin-bottom:7px}
.final-cta .ticks{margin:22px 0 22px}
.final-photo{position:absolute;right:0;top:0;width:430px;height:100%;background:linear-gradient(180deg,#e2dedb,#d88b7c 60%,#c9a98a)}

/* footer */
.site-footer{height:244px;background:var(--footer);color:#c9ccd4;display:flex;padding:60px 135px 0;gap:0}
.site-footer h4{color:var(--white);font-size:18px;font-weight:500;margin-bottom:14px}
.site-footer p{font-size:12px;line-height:1.55}
.foot-col{width:315px}
.foot-col a{color:var(--green);text-decoration:none}
.social{width:20px;height:20px;border-radius:50%;background:var(--white);margin-top:10px}
</style>
</head>
<body>

<header class="site-header">
  <div class="brand"><span class="brand-square"></span><span class="brand-name">Tuvelo</span></div>
  <nav class="main-nav">
    <span class="active">Home</span><span>Why Bamboo</span><span>About Us</span><span>Reviews</span>
    <a class="btn" href="#">Buy Now</a>
  </nav>
</header>

<section class="hero">
  <div class="hero-photo" role="img" aria-label="Photo of feet in cosy knitted socks on a bed"></div>
  <div class="hero-content">
    <h1>Enjoy Your First Pair of Bamboo Socks for Only 20 PKK</h1>
    <ul class="ticks">
      <li><svg width="14" height="14" viewBox="0 0 14 14"><path d="M1 7l4 4 8-9" fill="none" stroke="#fff" stroke-width="2"/></svg>We have been working on textile for more than 10 years</li>
      <li><svg width="14" height="14" viewBox="0 0 14 14"><path d="M1 7l4 4 8-9" fill="none" stroke="#fff" stroke-width="2"/></svg>All products meet our high quality standards</li>
      <li><svg width="14" height="14" viewBox="0 0 14 14"><path d="M1 7l4 4 8-9" fill="none" stroke="#fff" stroke-width="2"/></svg>Our customers loves us, and we have a 5 stars rating at scorevane.com</li>
    </ul>
    <div class="hero-actions">
      <a class="btn" href="#">Buy Now</a>
      <a class="btn btn-ghost" href="#">&#9654;&nbsp; Watch Video</a>
    </div>
    <p class="small-note">Shipment included</p>
  </div>
</section>

<section class="why">
  <h2 class="section-title">Why Bamboo Clothing?</h2>
  <p class="lead">It was only in 2011 that the Northfield University discovered how you can make fabric from bamboo stems. Now bamboo has the potential to become the textile of the future.</p>
  <div class="benefits">
    <div class="benefit">
      <svg width="34" height="30" viewBox="0 0 34 30"><path d="M11 2l-9 5 3 7 4-2v16h16V12l4 2 3-7-9-5c-1 3-3 5-6 5s-5-2-6-5z" fill="none" stroke="#2fb37c" stroke-width="2"/></svg>
      <h3>Comfortable</h3><p>Bamboo fabric breathes making you comfortable in garments made in this.</p>
    </div>
    <div class="benefit">
      <svg width="30" height="30" viewBox="0 0 30 30"><path d="M5 25C5 12 14 5 26 4c0 13-8 21-21 21zM5 25l12-12" fill="none" stroke="#2fb37c" stroke-width="2"/></svg>
      <h3>Eco-friendly</h3><p>Bamboo is a very fast growing tropical forest product, which does not impact the soil of sublimities.</p>
    </div>
    <div class="benefit">
      <svg width="30" height="30" viewBox="0 0 30 30"><path d="M6 4h18v22H6z M10 10h10M10 15h10M10 20h6" fill="none" stroke="#2fb37c" stroke-width="2"/></svg>
      <h3>Exquisitely soft</h3><p>The moment you wear it next to your skin you will notice the difference between other fabrics.</p>
    </div>
    <div class="benefit">
      <svg width="30" height="30" viewBox="0 0 30 30"><path d="M15 3l11 22H4z M9 18h12" fill="none" stroke="#2fb37c" stroke-width="2"/></svg>
      <h3>Thermo-control</h3><p>Bamboo fabric is warm thanks to its hollow microfiber, yet is also breathable.</p>
    </div>
  </div>
</section>

<section class="feature">
  <div class="photo" role="img" aria-label="Photo of patterned purple socks and dark leather shoes" style="background:linear-gradient(135deg,#2a2a2a,#6e5a6a 55%,#1d1d1d)"></div>
  <div class="text alt"><h3>Strong Material</h3><p>Bamboo fabric is lightweight yet strong. The natural processing of bamboo allows the fibre to remain strong to produce an extremely high quality product. This process gives a material that is very durable.</p></div>
</section>

<section class="feature left-text">
  <div class="text"><h3>Completely Clean</h3><p>Bamboo fibers doesnt under go much chemical processing to make the fabric, so you can easily wear it without causing any allergic irritation to the skin that is more prevalent with heavily processed fabrics.</p></div>
  <div class="photo" role="img" aria-label="Photo of a family relaxing together on a light sofa" style="background:linear-gradient(135deg,#e9e4de,#c9b7a3 50%,#f4efe9)"></div>
</section>

<section class="feature">
  <div class="photo" role="img" aria-label="Photo of feet in knitted socks in front of a fireplace" style="background:linear-gradient(90deg,#1f150e,#a2481a 45%,#3a2b22)"></div>
  <div class="text"><h3>Water Absorbent</h3><p>Bamboo fibers are water absorbent. So if you live in a humid environment this is the fabric for you. Think of the sweat it will absorb and evaporate out of your body.</p></div>
</section>

<section class="offer-band">
  <div class="offer-pct">-90%</div>
  <div class="offer-title">Get Your First Pair of Socks With an Exclusive Discount</div>
  <div class="offer-cta"><a class="btn" href="#">Buy Now</a><p class="small-note">Shipment included</p></div>
</section>

<section class="facts">
  <h2>A Few Facts About Tuvelo</h2>
  <p class="intro">We have been working on textile for more than 10 years. This ensures that all products meet our high quality standards.</p>
  <div class="fact-row">
    <div class="fact"><div class="fact-icon"><svg width="30" height="28" viewBox="0 0 34 30"><path d="M11 2l-9 5 3 7 4-2v16h16V12l4 2 3-7-9-5c-1 3-3 5-6 5s-5-2-6-5z" fill="#4fa6ea"/></svg></div><p>Our mission is to give our customers access to quality products at a reasonable price.</p></div>
    <div class="fact"><div class="fact-icon"><svg width="28" height="28" viewBox="0 0 28 28"><rect x="4" y="3" width="20" height="22" fill="#4fa6ea"/><path d="M9 18l4-5 3 3 4-6" stroke="#fff" stroke-width="2" fill="none"/></svg></div><p>We know that the properties of bamboo are absolutely amazing and can reduce, for example, sweaty and sour toes.</p></div>
    <div class="fact"><div class="fact-icon"><svg width="28" height="28" viewBox="0 0 28 28"><circle cx="14" cy="11" r="8" fill="#4fa6ea"/><path d="M9 17l-3 9 8-4 8 4-3-9" fill="#4fa6ea"/></svg></div><p>We shop directly with the factories. This ensures the highest quality at a competitive price.</p></div>
  </div>
</section>

<section class="video">
  <div class="leaf" role="img" aria-label="Green leaves decoration" style="left:0;top:0;width:230px;height:200px;background:radial-gradient(ellipse at 20% 20%,#5f8a3a,rgba(95,138,58,0) 70%)"></div>
  <div class="leaf" role="img" aria-label="Green leaves decoration" style="right:0;bottom:0;width:200px;height:260px;background:radial-gradient(ellipse at 80% 70%,#5f8a3a,rgba(95,138,58,0) 70%)"></div>
  <h2 class="section-title">A Short Video About Our Work</h2>
  <p class="lead">We sell stockings, t-shirts, sweaters and men's boxershorts. If you choose our subscription service, the products will come to you automatically.</p>
  <div class="video-frame" role="img" aria-label="Video still of packed clothes and shoes on a wooden floor">
    <svg class="play" width="60" height="60" viewBox="0 0 60 60"><circle cx="30" cy="30" r="30" fill="#2fb37c"/><path d="M24 18l18 12-18 12z" fill="#fff"/></svg>
  </div>
</section>

<section class="rating">
  <div class="stars">★★★★★</div>
  <h2 class="section-title">We Have a 5 Stars Rating</h2>
  <p class="lead">You're in a good company. Here are some important facts and testimonials about us.</p>
  <div class="reviews">
    <span class="arrow" style="left:105px">‹</span>
    <div class="review"><div class="reviewer"><span class="avatar"></span><div><strong>Ned Varley</strong><span>★★★★★</span></div></div><p>Lorem ipsum dolor sit amet, consetetur sadipscing elitr, sed diam nonumy eirmod tempor invidunt ut labore et dolore magna aliquyam erat, sed diam voluptua. At vero eos et accusam et justo duo.</p></div>
    <div class="review"><div class="reviewer"><span class="avatar"></span><div><strong>Ned Varley</strong><span>★★★★★</span></div></div><p>Lorem ipsum dolor sit amet, consetetur sadipscing elitr, sed diam nonumy eirmod tempor invidunt ut labore et dolore magna aliquyam erat, sed diam voluptua. At vero eos et accusam et justo duo.</p></div>
    <div class="review"><div class="reviewer"><span class="avatar"></span><div><strong>Ned Varley</strong><span>★★★★★</span></div></div><p>Lorem ipsum dolor sit amet, consetetur sadipscing elitr, sed diam nonumy eirmod tempor invidunt ut labore et dolore magna aliquyam erat, sed diam voluptua. At vero eos et accusam et justo duo.</p></div>
    <span class="arrow" style="right:105px">›</span>
  </div>
  <a class="btn" href="#">More Reviews</a>
</section>

<section class="final-cta">
  <div class="final-photo" role="img" aria-label="Photo of a smiling woman in a knitted hat holding a paper shopping bag"></div>
  <h2>Get Your First Pair of Bamboo Socks for Only 20 PKK</h2>
  <ul class="ticks">
    <li><svg width="14" height="14" viewBox="0 0 14 14"><path d="M1 7l4 4 8-9" fill="none" stroke="#2fb37c" stroke-width="2"/></svg>Powerfully insulating - keeps you cooler in summer and warmer in winter</li>
    <li><svg width="14" height="14" viewBox="0 0 14 14"><path d="M1 7l4 4 8-9" fill="none" stroke="#2fb37c" stroke-width="2"/></svg>Antibacterial - keeps you odor free and feeling and smelling fresh</li>
    <li><svg width="14" height="14" viewBox="0 0 14 14"><path d="M1 7l4 4 8-9" fill="none" stroke="#2fb37c" stroke-width="2"/></svg>Most eco-friendly fabric on the planet - help save your planet</li>
  </ul>
  <a class="btn" href="#" style="padding:11px 64px">Buy Now</a>
  <p class="small-note">Shipment included</p>
</section>

<footer class="site-footer">
  <div class="foot-col"><h4>About us</h4><p>At Tuvelo.dk we are specialized in basic products in bamboo. We sell stockings, t-shirts, sweaters and men's boxershorts.</p><div class="social"></div></div>
  <div class="foot-col"><h4>Contact us</h4><p>Any questions? Then e-mail <a href="#">info@tuvelo.dk</a><br>or call us on +45 20 40 60 80<br><br>Or send us a letter to Tuvelo<br>Lindevej 12<br>7100 Ostby</p></div>
  <div class="foot-col"><h4>Navigation</h4><p>Home &nbsp;/&nbsp; Why Bamboo &nbsp;/&nbsp; About &nbsp;/&nbsp; Reviews</p></div>
</footer>

</body>
</html>
```